Willow Crest Brand - Bag Design

We are a company dealing with nuts, grains and seeds and are looking for a design for our retail bag packaging that will be consistent across all our product range. We are currently differentiating in way of color but please feel free to be more creative if you wish. Sample of products include pumpkin seeds, rolled oats, almonds, etc.
Design Idea: Hygienic, Natural (from Nature), Quality & Upscale, Simple & Clean design
Target Market: High-end Markets, end-users of A/B type.
1. Bag size is 210 mm (width) * 310 mm (length). Material is OPP or multi-layer PP.
2. Front must have clear window to show packed products. Back clear window is optional.
3. Front side must have logo that stands out (Willow Crest) as attached.
4. Front side must have product name and net weight.
5. Back side must have enough space for Nutrition Fact, product descriptions (110 mm * 100 mm), and barcode.
6. Back side must have white space to print production and expiry dates about 25 mm * 30 mm.
7. Top and bottom of bag must be opaque and not show product.
Reason: Extended period for more new ideas and also for requested modification.
Target Market(s)
Premium market. Type A to B customers as well as professional clients. The product is not a snack. It is for cooking or baking.
Industry/Entity Type
Food Store
Requirements
Must have
- Look unique and stand out from others in the market.
- The colors of the word "Willow Crest" and the blue air-brush in the logo can be changed.
Nice to have
- See project description
Should not have
- See project description

```html
<!DOCTYPE html>
<html lang="en">
<head>
<meta charset="utf-8">
<title>Willow Crest – Pumpkin Seeds Bag</title>
<link rel="stylesheet" href="https://fonts.googleapis.com/css2?family=Courgette&family=Roboto+Condensed:wght@700&display=swap">
<style>
  :root {
    --backdrop: #d9d9d9;
    --gold-light: #ffe24a;
    --gold: #f5c400;
    --gold-deep: #d9a300;
    --label-white: #f4f4f4;
    --ribbon-red: #e0302a;
    --ribbon-dark: #a8161a;
    --ribbon-light: #f27a70;
    --seed-cream: #f1e8d4;
    --seed-mid: #e2d3b3;
    --seed-shadow: #bfa97f;
    --ink-olive: #3a3310;
    --text-white: #ffffff;
  }
  * { margin: 0; padding: 0; box-sizing: border-box; }
  html, body {
    width: 960px; height: 1200px; overflow: hidden;
    background: var(--backdrop);
  }
  .bag-front {
    position: absolute; left: 77px; top: 0;
    width: 806px; height: 1200px;
    background:
      repeating-linear-gradient(135deg, rgba(255,255,255,0.14) 0 34px, rgba(0,0,0,0) 34px 68px),
      linear-gradient(90deg, var(--gold-deep) 0%, var(--gold) 18%, var(--gold-light) 50%, var(--gold) 82%, var(--gold-deep) 100%);
  }
  .brand-label {
    position: absolute; left: 153px; top: 116px;
    width: 498px; height: 400px;
    background: linear-gradient(180deg, #fafafa, var(--label-white) 60%, #e9e9e9);
    display: flex; align-items: center; justify-content: center; gap: 18px;
    padding-top: 60px;
  }
  .brand-mark {
    width: 40px; height: 40px; border-radius: 50%;
    background: var(--ribbon-red);
    flex: none;
  }
  .brand-name {
    font-family: "Courgette", cursive;
    font-size: 66px; line-height: 1; color: var(--ribbon-red);
    white-space: nowrap;
  }
  .product-ribbon {
    position: absolute; left: 111px; top: 489px;
    width: 582px; height: 161px;
  }
  .product-name {
    position: absolute; left: 111px; top: 538px; width: 582px;
    text-align: center;
    font-family: "Courgette", cursive;
    font-size: 56px; line-height: 1.2; color: var(--text-white);
  }
  .product-window {
    position: absolute; left: 143px; top: 650px;
    width: 516px; height: 364px;
    background:
      radial-gradient(ellipse 35% 30% at 30% 35%, rgba(255,252,242,0.9), rgba(255,252,242,0) 100%),
      radial-gradient(ellipse 30% 28% at 72% 65%, rgba(255,250,238,0.85), rgba(255,250,238,0) 100%),
      radial-gradient(ellipse 25% 22% at 60% 25%, rgba(205,185,145,0.55), rgba(205,185,145,0) 100%),
      radial-gradient(ellipse 28% 24% at 25% 78%, rgba(205,185,145,0.5), rgba(205,185,145,0) 100%),
      radial-gradient(ellipse at center, var(--seed-cream) 20%, var(--seed-mid) 70%, var(--seed-shadow) 110%);
  }
  .window-base {
    position: absolute; left: 143px; top: 1012px;
    width: 516px; height: 29px;
    background: linear-gradient(90deg, var(--ribbon-dark), var(--ribbon-red) 40%, var(--ribbon-light) 55%, var(--ribbon-red) 70%, var(--ribbon-dark));
  }
  .net-weight {
    position: absolute; left: 0; top: 1096px; width: 806px;
    text-align: center;
    font-family: "Roboto Condensed", sans-serif; font-weight: 700;
    font-size: 22px; letter-spacing: -0.3px; color: var(--ink-olive);
  }
</style>
</head>
<body>
  <main class="bag-front">
    <section class="brand-label">
      <span class="brand-mark"></span>
      <span class="brand-name">Willow Crest</span>
    </section>

    <svg class="product-ribbon" viewBox="0 0 582 161" aria-hidden="true">
      <defs>
        <linearGradient id="ribbonFace" x1="0" x2="1" y1="0" y2="0">
          <stop offset="0" stop-color="#a8161a"/>
          <stop offset="0.12" stop-color="#e0302a"/>
          <stop offset="0.5" stop-color="#f27a70"/>
          <stop offset="0.88" stop-color="#e0302a"/>
          <stop offset="1" stop-color="#a8161a"/>
        </linearGradient>
      </defs>
      <path d="M0 14 Q10 0 40 8 L40 150 Q12 146 0 158 Z" fill="#8d1216"/>
      <path d="M582 14 Q572 0 542 8 L542 150 Q570 146 582 158 Z" fill="#8d1216"/>
      <path d="M28 8 Q291 28 554 8 L554 150 Q291 170 28 150 Z" fill="url(#ribbonFace)"/>
    </svg>
    <h1 class="product-name">Pumpkin Seeds</h1>

    <div class="product-window" role="img" aria-label="Clear window showing a mass of whole cream-coloured pumpkin seeds"></div>
    <div class="window-base"></div>

    <p class="net-weight">Net Wt. 16 OZ (454g)</p>
  </main>
</body>
</html>
```